Trifold Leaflet - Osteopathy

Trifold Leaflet (A4 size paper) to provide information and promote an established English seafront osteopathy clinic.
I would like a simple modern design to reflect the seafront location and the caring nature of osteopathy treatment. The design needs to be not be generic or too corporate.
At the top of the front page in a large font should be the word "Osteopathy" as it will be displayed in a rack of leaflets (photo attached) and needs to be eye-catching.
I have attached a logo file and some examples of the kinds of designs that I like- but i'm very open to your expert ideas!
Also attached is a photo of the location- a bit of an ugly building but right on the beach, it would be great if this location could be emphasized!
The Word files: Leaflets word-inside.doc & Leaflets word-outside.doc uploaded show the content that I'd like- this is definitely not set in stone and I appreciate that less content is probably needed. Feel free to include/leave out whatever you feel is right.
More info on the practice can be found on my website:
www.marlowbayosteo.com
The pixelharbor images are ones that I have previously bought the rights to use, but only use them if you think they suit you design- I have included them i case they are of use to you.
Target Market(s)
Any adult.
Industry/Entity Type
Building
Look and feel

```html
<!DOCTYPE html>
<html lang="en">
<head>
<meta charset="utf-8">
<title>Osteopathy – Inside Spread</title>
<link rel="stylesheet" href="https://fonts.googleapis.com/css2?family=Arimo:wght@400;700&display=swap">
<style>
  :root {
    --paper: #ffffff;
    --teal: #8ecfbf;
    --teal-text: #86cbb9;
    --teal-strong: #5fb8a2;
    --panel-text: #ffffff;
    --skin: #d9b7a0;
    --skin-light: #efe0d4;
    --hair: #2b2522;
  }
  * { box-sizing: border-box; margin: 0; padding: 0; }
  html, body { width: 1200px; height: 859px; overflow: hidden; background: var(--paper); }
  body { font-family: "Arimo", Arial, sans-serif; color: var(--teal-text); position: relative; }

  .photo { position: absolute; }
  .photo--top { left: 415px; top: 38px; width: 347px; height: 165px;
    background: linear-gradient(100deg, var(--skin-light) 0%, var(--skin) 40%, #3a302b 60%, var(--skin) 80%, var(--skin-light) 100%); }
  .photo--side { left: 38px; top: 518px; width: 294px; height: 96px;
    background: linear-gradient(90deg, #f4ece6 0%, var(--skin) 35%, var(--skin) 65%, #f4ece6 100%); }
  .photo--wide { left: 38px; top: 628px; width: 741px; height: 181px;
    background: linear-gradient(90deg, var(--skin-light) 0%, var(--skin) 45%, var(--skin) 60%, var(--hair) 80%, var(--hair) 100%); }
  .rule { position: absolute; left: 415px; top: 212px; width: 347px; height: 1px; background: var(--teal); }

  .column { position: absolute; font-size: 9.6px; line-height: 1.38; }
  .column p { margin-bottom: 12px; }
  .column--intro { left: 55px; top: 219px; width: 300px; }
  .column--regulation { left: 436px; top: 219px; width: 326px; }
  .keyword { color: var(--teal-strong); font-weight: 700; }
  .section-title { font-size: 12.5px; font-weight: 700; color: var(--teal-strong); margin-bottom: 12px; }
  .plain-list { list-style: none; }

  .visit-panel { position: absolute; left: 802px; top: 21px; width: 353px; height: 813px;
    background: var(--teal); color: var(--panel-text); padding: 150px 14px 0 14px; }
  .visit-panel h2 { font-size: 13px; font-weight: 700; margin-bottom: 18px; }
  .visit-panel h3 { font-size: 12.5px; font-weight: 700; margin-top: 0; }
  .visit-panel p { font-size: 9.6px; line-height: 1.38; margin-bottom: 14px; }
  .web-address { position: absolute; left: 0; right: 0; top: 762px; text-align: center; font-size: 14px; }
</style>
</head>
<body>
  <div class="photo photo--top" role="img" aria-label="Photo: patient lying face down receiving neck and shoulder treatment"></div>
  <div class="rule"></div>

  <section class="column column--intro">
    <p>Much of the pain and disability we suffer stems from abnormalities in our body's structure and function.</p>
    <p><span class="keyword">Osteopathy</span> treats problems related to the musculoskeletal system, muscles, ligaments, nerves and joints, and helps the body's natural healing ability to correct itself and relieve the pain caused by dysfunction.</p>
    <p>When the body is balanced and efficient, just like a tuned engine, it will function with minimum wear and tear, requiring less energy to operate correctly.</p>
    <p>Natural, Drug Free, Pain Relief</p>
    <ul class="plain-list">
      <li>Treating:</li>
      <li>Arthritis &amp; Joint Pain</li>
      <li>Back &amp; Neck Pain</li>
      <li>Frozen Shoulder</li>
      <li>Sports Injury</li>
      <li>Sciatica</li>
    </ul>
  </section>

  <section class="column column--regulation">
    <h2 class="section-title">Osteopathy is Regulated and safe</h2>
    <p><span class="keyword">Osteopathy</span> is one of only two complementary and alternative medicines (CAMs) that are regulated under UK law. This regulation works in much the same way as regulation for medical doctors.</p>
    <p>The OSC regulates the Osteopathic profession in the UK, maintaining a Statutory Register of those entitled to practise. Only practitioners meeting the high standards of safety and competency are eligible to join this register. All Osteopaths are required to undertake a certain amount of CPD (Continuing Professional Development) each year to keep up to date with new research and practise within the profession.</p>
    <p>As Recommended by The Guild of GP's</p>
    <p><span class="keyword">Osteopathy</span> is used to treat many problems related to the musculoskeletal system. Osteopathic manipulation has been recommended by The National Board for Health and Care Standards (NBHCS) and The Guild of General Practitioners (GGP) for the treatment of low back pain.</p>
  </section>

  <div class="photo photo--side" role="img" aria-label="Photo: hands massaging a patient's shoulder"></div>
  <div class="photo photo--wide" role="img" aria-label="Photo: osteopath's hands working on a patient's neck and upper back"></div>

  <aside class="visit-panel">
    <h2>Your first visit</h2>
    <h3>Medical History</h3>
    <p>On your first visit, we will ask you lots of questions to build up a detailed medical history. Your past medical history can often be relevant to current problems you are experiencing and may be discussed. We may ask about past illnesses, operations, injuries, accidents and medications.</p>
    <h3>Assessment</h3>
    <p>Based on your medical history, we will perform some tests to help form a diagnosis of your current condition. Typical tests include range and quality of joint movements, tenderness to palpation, muscle tone and strength, reflexes and blood pressure.</p>
    <h3>Treatment</h3>
    <p>Supported by an in depth knowledge of functional anatomy and physiology the detailed examination enables the Osteopath to diagnose safely and choose the right treatment to address the causes of the patient's symptoms. Treatment involves gentle, manual techniques – easing pain, reducing swelling and improving mobility. Osteopathy is a 'package' of care that includes skilled mobilising and manipulative techniques, reinforced by guidance on diet and exercise.<br>For further information, or if you have any questions regarding Osteopathy, please contact us. We are here to help.</p>
    <div class="web-address">www.marlowbayosteo.com</div>
  </aside>
</body>
</html>
```